Design a New Business Card for Our Company

We are looking for fresh, unique, and a modern business card that reflects our roots as digital marketing agency focused on SEM.

Industry/Entity Type

Marketing

Contact Information for Business Card

looking for very unique out of the box designs. clean and modern that compliments our logo

Requirements
Must have
• colors should match our logo
• Front should have name, address, email, and phone/fax of the person, phone/fax are the same number
• back should have our url

```html
<!DOCTYPE html>
<html lang="en">
<head>
<meta charset="utf-8">
<title>Northfield Solutions – Business Card</title>
<link href="https://fonts.googleapis.com/css2?family=Arimo:wght@400;700&display=swap" rel="stylesheet">
<style>
  :root {
    --stage: #3a332f;
    --card: #1c1c1d;
    --card-edge: #2a2a2b;
    --text: #e6e6e6;
    --muted: #9a9a9a;
    --accent: #4a90d9;
    --rule: #cfcfcf;
  }
  * { margin: 0; padding: 0; box-sizing: border-box; }
  html, body { width: 1200px; height: 787px; overflow: hidden; }
  body {
    background: var(--stage);
    font-family: "Arimo", Arial, sans-serif;
    display: flex;
    align-items: center;
    justify-content: center;
    gap: 44px;
  }
  .card {
    position: relative;
    width: 520px;
    height: 298px;
    background: var(--card);
    border: 1px solid var(--card-edge);
    box-shadow: 0 10px 28px rgba(0,0,0,.45);
    overflow: hidden;
  }
  .brand {
    display: flex;
    align-items: center;
    gap: 12px;
    white-space: nowrap;
  }
  .brand-dot {
    width: 30px; height: 30px;
    border-radius: 50%;
    flex: none;
  }
  .brand-name {
    font-weight: 700;
    font-size: 32px;
    letter-spacing: -0.5px;
    line-height: 1;
  }
  /* back side */
  .card-back .brand { position: absolute; left: 48px; top: 74px; }
  .card-back .brand-dot { background: var(--muted); }
  .card-back .brand-name { color: var(--muted); }
  .card-back .url {
    position: absolute; left: 50px; bottom: 56px;
    color: var(--text);
    font-size: 13px;
    letter-spacing: 4px;
  }
  /* front side */
  .card-front .brand { position: absolute; left: 30px; top: 127px; gap: 10px; }
  .card-front .brand-dot { width: 22px; height: 22px; background: var(--accent); }
  .card-front .brand-name { color: var(--accent); font-size: 20px; letter-spacing: -0.3px; }
  .divider {
    position: absolute; left: 296px; top: 92px;
    width: 1px; height: 150px;
    background: linear-gradient(to bottom, transparent, var(--rule) 20%, var(--rule) 80%, transparent);
  }
  .contact {
    position: absolute; left: 312px; top: 94px;
    color: var(--text);
    font-size: 14px;
    line-height: 1.3;
    white-space: nowrap;
  }
  .contact-name { font-size: 17px; font-weight: 700; }
  .contact-title { color: var(--accent); font-size: 14px; margin-bottom: 6px; }
  .contact-address { margin-bottom: 4px; }
  .contact-line { display: flex; align-items: center; gap: 8px; }
  .contact-line svg { width: 14px; height: 14px; fill: var(--muted); flex: none; }
</style>
</head>
<body>
  <section class="card card-back" aria-label="Card back">
    <div class="brand">
      <span class="brand-dot"></span>
      <span class="brand-name">Northfield Solutions</span>
    </div>
    <p class="url">www.northfield.com</p>
  </section>

  <section class="card card-front" aria-label="Card front">
    <div class="brand">
      <span class="brand-dot"></span>
      <span class="brand-name">Northfield Solutions</span>
    </div>
    <div class="divider"></div>
    <div class="contact">
      <p class="contact-name">Mark Ellis</p>
      <p class="contact-title">President</p>
      <p class="contact-address">2417 Harborview Lane<br>Cedar Grove, NJ 07009</p>
      <p class="contact-line">
        <svg viewBox="0 0 16 16" aria-hidden="true"><path d="M3 1h3l1.5 4-2 1.3a9 9 0 0 0 4.2 4.2L11 8.5l4 1.5v3a2 2 0 0 1-2 2A12 12 0 0 1 1 3a2 2 0 0 1 2-2z"/></svg>
        555 0142 7781
      </p>
      <p class="contact-line">
        <svg viewBox="0 0 16 16" aria-hidden="true"><path d="M4 1h8v4H4zM1 6h14v7h-3v2H4v-2H1zM5 11v3h6v-3z"/></svg>
        555 0198 3304
      </p>
      <p class="contact-line">
        <svg viewBox="0 0 16 16" aria-hidden="true"><path d="M1 3h14v10H1zM2 4l6 5 6-5v-.2H2z"/></svg>
        mark@northfield.com
      </p>
    </div>
  </section>
</body>
</html>
```